Movie poster for Indie Horror movie

Looking for a movie poster for my indie project. Details below...

Tagline
In Hollywood, even nightmares have producers.

Here is a logline for the project:
On a family trip to Hollywood, a rebellious young director joins her stepbrother’s immersive horror film—only to find herself trapped in a deadly game where fiction and reality blur. As bodies fall and masked men close in, she must decide whether to play the victim or rewrite the ending before the final act consumes her.

Synopsis:
When Tessa, a fiercely ambitious young director with a taste for chaos, joins her family on a vacation to Hollywood, she’s lured into her stepbrother Anselm’s latest project—a fully immersive horror experience designed to blur the line between performance and reality. At first, Tessa revels in the eerie theatrics: masked figures in the shadows, a break-in at their rental home, and Anselm’s cryptic direction. It all feels like the perfect stage for her breakout moment.
But when her parents turn up dead and Anselm disappears, Tessa’s grip on the narrative begins to unravel. As the terror escalates and masked men close in, she’s forced into a brutal fight for survival—only to uncover the twisted truth: Anselm, desperate to shed his golden-boy persona, has engineered the chaos alongside his enigmatic collaborator, Corin. Their goal? To craft the ultimate psychological horror, with Tessa as its unwitting star.
Now, trapped in a nightmare that refuses to cut, Tessa must decide whether to surrender to the role written for her—or seize control and rewrite the ending before it’s too late.

Idea
Obviously, the poster design should be scary, should reflect the story, should be something that people notice.

I'm a fan of simple and clean (think the Dusktide movie poster). I'm not a visual person, but I thought we could utilize the two characters in masks (which I will attach). You can use one or both (maybe put them together?) or neither.

The design should incorporate the title: Hollow Lantern and have an area for the billing block (credits) on the bottom.

Feel free to msg us if you have any questions.

Target Market(s)

Horror fans

Industry/Entity Type

Movies

Requirements
Must have
• Must inspire fear or thrills

```html
<!DOCTYPE html>
<html lang="en">
<head>
<meta charset="utf-8">
<title>Hollow Lantern – Poster</title>
<link rel="stylesheet" href="https://fonts.googleapis.com/css2?family=Stardos+Stencil:wght@700&family=Poppins:wght@500;600;700&display=swap">
<style>
  :root {
    --stage: #1a1a1a;
    --poster: #000000;
    --blood: #e3120f;
    --ink: #ffffff;
    --muted: #8a8a8a;
    --cast-first: #cfcfcf;
  }
  * { margin: 0; padding: 0; box-sizing: border-box; }
  html, body {
    width: 1200px; height: 1001px; overflow: hidden;
    background: var(--stage);
  }
  .poster {
    position: absolute; left: 333px; top: 0;
    width: 534px; height: 1001px;
    background: var(--poster);
    font-family: "Poppins", sans-serif;
    color: var(--ink);
  }
  .cast {
    position: absolute; top: 213px; left: 0; width: 100%;
    font-size: 7.5px; font-weight: 500; letter-spacing: .1px;
  }
  .cast-name { position: absolute; color: var(--cast-first); text-transform: uppercase; white-space: nowrap; }
  .cast-name b { color: var(--muted); font-weight: 600; }
  .cast-name:nth-child(1) { left: 113px; }
  .cast-name:nth-child(2) { left: 226px; }
  .cast-name:nth-child(3) { left: 358px; }
  .key-art {
    position: absolute; left: 150px; top: 276px;
    width: 250px; height: 390px;
    background:
      radial-gradient(ellipse 48% 46% at 50% 52%, #e01515 0%, #a80d0d 55%, rgba(90,0,0,.6) 80%, rgba(0,0,0,0) 100%);
  }
  .credit-line {
    position: absolute; top: 675px; width: 100%;
    text-align: center; font-size: 10.5px; font-weight: 700; text-transform: uppercase;
  }
  .title {
    position: absolute; top: 690px; width: 100%;
    text-align: center;
    font-family: "Stardos Stencil", serif; font-weight: 700;
    font-size: 50px; line-height: 1; letter-spacing: -1px;
    color: var(--blood); text-transform: uppercase;
  }
  .billing {
    position: absolute; top: 776px; width: 100%;
    text-align: center; text-transform: uppercase;
    font-size: 7.2px; font-weight: 700; line-height: 10.4px;
    color: #e6e6e6;
  }
  .billing small { font-size: 4.2px; font-weight: 500; color: #bdbdbd; letter-spacing: .1px; }
</style>
</head>
<body>
  <main class="poster">
    <div class="cast">
      <span class="cast-name">Ilse <b>Vorberg</b></span>
      <span class="cast-name">Marit <b>Holmqvist</b></span>
      <span class="cast-name">Aldo <b>Ferrant</b></span>
    </div>

    <div class="key-art" role="img" aria-label="Red-tinted photograph of a pointed-eared animal mask with dark eye holes"></div>

    <p class="credit-line">A film by Nolan Vey</p>
    <h1 class="title">Hollow Lantern</h1>

    <div class="billing">
      <p>Studio Greyfen <small>production in association with</small> Kellmarch <small>productions</small> “Velvet Hour”</p>
      <p><small>casting by</small> Ezra Colm <small>associate producer</small> Dara Whitlow <small>co-producer</small> Pia Renholt</p>
      <p><small>produced by</small> Joan Hadley and Ross Keller <small>written and directed by</small> Owen Marsh</p>
    </div>
  </main>
</body>
</html>
```